Church Website with Home Page and Member Sermon Library

I am in need of an updated design for our church website. This will include 4 pages (outlined below). We are a conservative, evangelical, Christian church. The site should be modern and clean, while still reflecting our conservative values. I already have a logo for our church, and I want the site to incorporate the logo, and match the logo/branding. Stock photos are allowed if needed, but I have uploaded some images of our church and would prefer those images to be used if possible. Any stock photos used should not include any people in the photos (scenery, nature, buildings, animals, etc. are fine).

The site will need 4 pages: Home, Support Us (Donate), Login, and Recording Library.

Page 1: Home
The home page should include the following sections:

- Navigation: Should include links to each section of the home page plus a "listen live" link which will take the user to a live-streaming site and a "support us" link which will take the user to a support/donate page.

- Announcements: Can be either a banner or some other design, but there needs to be some way for us to post announcements for visitors to see. I'm open for creative ideas in this section, but would like it not to take up a lot of room on the page.

- About Us: Should include address, service times (see attached document), and information about the church.

- Pastor Bio: A section that introduces our pastor and gives a short bio about our pastor. Would like this section to include a picture of our pastor. Somewhere in this section I would like to include this Bible reference: "And I will give you pastors according to mine heart, which shall feed you with knowledge and understanding. Jer 3:15 LPW"

- Articles of Faith (What We Believe): This should include several sub-sections each with a heading, body, and possibly 1 or more scripture references. I have attached a document to the brief that includes our articles of faith. Feel free to be creative with this section in how you lay these out and format them.

- Support Us: A small section that explains what kind of support someone can give and a link to a donation page. The link can say something like "Support Us" or "Donate Now".

- Contact form: A contact form that allows the visitor to send us a message. The contact form should ask for name, email, phone, and message.

- Footer: A footer that will be displayed on all pages of the site. This should include at a minimum a link to the home page (or a link to each individual section in the home page if you prefer), a link to "listen live", a link to "support us", a link to "contact us" (or you can put the contact form directly in the footer if you prefer), the address, and a "member login" link.

Page 2: Support Us
The donation page should include a form the visitor can fill out to make a donation. We will embed a third party form later. For this design, please just mock out the design with a basic form asking for name, phone, and email.

Page 3: Login
The recording library (detailed below) will require members to login with a shared numeric code before accessing the page. We need a design for a login screen. The screen should include navigation/footer just like all other pages, but the body of the login page will consist only of a form that asks the user to enter the access code and then a "login" button.

Page 4: Recording Library

The library page is a member-only page that will require a shared, numeric pass code to access. On this page, members will be able to access a filterable list of past sermons. The page by default should display most recent sermons, but should also include a search form that allows the member to filter the sermon list to find a particular sermon. The search form should allow the user to select a filter type (e.g. Speaker name, date, event, etc.) and type in a value to search. They should be able to add multiple filters and remove filters that have been added. Each sermon that is displayed in the result list should include basic information such as title, date, speaker, tags, etc. along with a download icon, and an embedded audio player where they can click a play button to stream it on-demand. Each sermon should also have clickable tags associated with it that can be used to find related sermons.
Updates

I have uploaded several images of our church. Feel free to incorporate these into your design if possible.

Target Market(s)

Church Members

Industry/Entity Type

Religion

Number of Pages Required

4 page

Font styles to use
Sans Serif

Colors

Designer to choose colors to be used in the design.

Requirements
Must have
• Must incorporate the logo (attached)
Nice to have
• Would like the design to incorporate pictures of our church (attached) instead of stock photos if possible.
Should not have
• Please avoid an overly cluttered design. Stock photos used should not include any people in the photos.

```html
<!DOCTYPE html>
<html lang="en">
<head>
<meta charset="utf-8">
<title>Grace Harbor Church</title>
<link rel="stylesheet" href="https://fonts.googleapis.com/css2?family=Cinzel:wght@400;600;700&family=Lato:wght@400;700;900&display=swap">
<style>
:root{
  --teal:#1db3d2;
  --teal-dark:#0f97b8;
  --olive:#6e7b3b;
  --green:#3f6b2b;
  --green-light:#7aa35a;
  --ink:#2b2b2b;
  --grey:#6a6a6a;
  --faint:#f1f1f1;
  --white:#ffffff;
}
*{box-sizing:border-box;margin:0;padding:0}
html,body{width:1200px;height:3896px;overflow:hidden}
body{position:relative;background:var(--white);font-family:"Lato",Arial,sans-serif;color:var(--ink)}
.abs{position:absolute}

/* hero */
.hero{left:0;top:0;width:1200px;height:700px;background:linear-gradient(180deg,#8fa7c0 0%,#d9b59b 32%,#f2c48f 52%,#c98a5a 72%,#3d3a33 100%)}
.service{left:40px;top:26px;color:var(--white);font-size:15px;line-height:1.35}
.service h4{font-family:"Lato",sans-serif;font-weight:900;font-size:20px;letter-spacing:.5px;margin-bottom:4px}
.brand{left:500px;top:24px;width:200px;text-align:center;color:var(--teal)}
.brand .mark{width:40px;height:40px;border-radius:50%;background:var(--teal);margin:0 auto 8px}
.brand .name{font-family:"Cinzel",serif;font-weight:600;font-size:26px;line-height:1.05}
.nav{right:40px;top:60px;display:flex;gap:34px;align-items:center;color:var(--white);font-weight:700;font-size:17px;letter-spacing:.5px}
.pill{display:inline-block;border-radius:40px;font-weight:700;text-transform:uppercase;letter-spacing:1px;color:var(--white)}
.nav .pill{background:var(--teal);padding:10px 22px;font-size:15px}
.hero-title{left:0;top:300px;width:1200px;text-align:center;color:var(--white);font-family:"Cinzel",serif;font-weight:700;font-size:66px;line-height:1.12;text-shadow:0 2px 10px rgba(0,0,0,.25)}

/* tagline band */
.band{left:0;top:630px;width:1140px;height:136px;background:var(--teal);border-radius:0 120px 0 0;color:var(--white);padding:22px 0 0 148px}
.band h2{font-family:"Cinzel",serif;font-weight:600;font-size:34px;margin-bottom:10px}
.band p{font-weight:700;font-size:18px;line-height:1.35;width:640px}
.donate-circle{left:840px;top:660px;width:148px;height:148px;border-radius:50%;background:var(--olive);color:var(--white);display:flex;align-items:center;justify-content:center;font-family:"Cinzel",serif;font-size:17px;border:6px solid var(--white)}

/* about */
.ghost{color:var(--faint);font-family:"Cinzel",serif;font-weight:700;font-size:120px;letter-spacing:4px}
.about-ghost{left:140px;top:810px}
.about-title{left:148px;top:960px;color:var(--teal);font-family:"Cinzel",serif;font-weight:600;font-size:50px;line-height:1.1}
.about-lead{left:148px;top:1100px;width:340px;color:var(--teal);font-weight:900;font-size:21px;line-height:1.3}
.about-mark{left:490px;top:920px;width:210px;height:450px;background:linear-gradient(180deg,#d8f2f8,#bfe8f2)}
.about-copy{left:740px;top:960px;width:330px;font-size:15px;line-height:1.5;color:var(--ink)}
.about-copy p{margin-bottom:22px}

/* pastor */
.pastor{left:0;top:1520px;width:1200px;height:680px;background:linear-gradient(90deg,var(--green) 0%,#4f7b35 55%,var(--green-light) 100%)}
.pastor-ghost{left:40px;top:1720px;font-size:110px;color:rgba(255,255,255,.07);font-family:"Cinzel",serif;font-weight:700}
.pastor-title{left:148px;top:1700px;color:var(--white);font-family:"Cinzel",serif;font-weight:600;font-size:44px}
.pastor-copy{left:148px;top:1770px;width:310px;color:var(--white);font-size:14px;line-height:1.5}
.pastor-btn{left:148px;top:1890px;background:var(--olive);padding:10px 24px;font-size:13px;border:1px solid rgba(255,255,255,.4)}
.pastor-photo{left:560px;top:1620px;width:320px;height:580px;border-radius:160px 160px 0 0;background:#e6e6e6;color:#9a9a9a;font-size:22px;display:flex;align-items:center;justify-content:center}

/* articles */
.articles-title{left:0;top:2240px;width:1200px;text-align:center;color:var(--teal);font-family:"Cinzel",serif;font-weight:600;font-size:46px}
.articles-ghost{left:1130px;top:2300px;font-size:90px;color:var(--faint);font-family:"Cinzel",serif;font-weight:700;transform:rotate(90deg);transform-origin:left top}
.card{top:2320px;width:290px;height:374px;border:2px solid var(--teal);border-radius:10px;overflow:hidden;background:var(--white)}
.card .photo{height:158px}
.card .date{display:inline-block;margin:-16px 0 0 16px;position:relative;background:var(--olive);color:var(--white);font-size:12px;padding:6px 12px;border-radius:4px}
.card h3{font-size:17px;font-weight:900;color:var(--teal);line-height:1.3;padding:12px 18px 10px}
.card p{font-size:13px;line-height:1.5;color:var(--grey);padding:0 18px}
.card.one{left:152px}.card.two{left:456px}.card.three{left:760px}
.articles-btn{left:518px;top:2730px;background:var(--teal);padding:12px 28px;font-size:14px}

/* announcements */
.ann-title{left:0;top:2830px;width:1200px;text-align:center;color:var(--ink);font-family:"Cinzel",serif;font-weight:400;font-size:46px}
.ann-band{left:0;top:2900px;width:1200px;height:520px;background:linear-gradient(180deg,#55cbe2 0%,var(--teal) 60%,#15a7c7 100%);border-radius:260px 0 260px 0}
.ann-photo{left:120px;top:2900px;width:960px;height:520px;background:radial-gradient(ellipse at center,rgba(255,255,255,.18),rgba(255,255,255,0) 70%)}
.ann-heading{left:148px;top:3040px;width:470px;color:var(--white);font-weight:900;font-size:34px;line-height:1.2}
.ann-copy{left:148px;top:3140px;width:360px;color:var(--white);font-size:16px;line-height:1.4}
.ann-btn{left:148px;top:3220px;border:2px solid var(--white);padding:8px 22px;font-size:15px}
.subscribe{left:708px;top:3020px;width:300px;color:var(--white)}
.subscribe h3{font-weight:900;font-size:34px;margin-bottom:16px}
.field{height:36px;border:1px solid rgba(255,255,255,.7);border-radius:18px;color:var(--white);font-size:13px;padding:10px 18px;margin-bottom:16px;background:rgba(255,255,255,.12)}
.subscribe .pill{display:block;text-align:center;background:var(--olive);padding:10px 0;font-size:16px;margin-top:4px}

/* footer */
.foot-brand{left:150px;top:3520px;width:180px;text-align:center;color:var(--teal)}
.foot-brand .mark{width:46px;height:46px;border-radius:50%;background:var(--teal);margin:0 auto 10px}
.foot-brand .name{font-family:"Cinzel",serif;font-weight:600;font-size:26px;line-height:1.05}
.socials{display:flex;gap:8px;justify-content:center;margin-top:14px}
.socials span{width:24px;height:24px;border-radius:50%;background:var(--teal)}
.divider{top:3500px;width:2px;height:290px;background:var(--olive)}
.col{top:3510px;font-size:14px;line-height:1.5;color:var(--ink)}
.col h5{color:var(--teal);font-family:"Cinzel",serif;font-weight:600;font-size:20px;margin-bottom:10px;letter-spacing:.5px}
.col li{list-style:none;padding:8px 0;border-bottom:1px solid #ddd;font-size:14px}
.row{display:flex;gap:10px;margin-bottom:10px}
.row svg{flex:none;margin-top:3px}
.bottom{left:0;top:3820px;width:1200px;height:76px;border-top:1px solid #ddd}
.copyright{left:40px;top:3850px;font-size:13px;color:var(--grey)}
.foot-donate{left:910px;top:3838px;background:var(--olive);padding:12px 34px;font-size:15px;text-transform:none;letter-spacing:.5px}
</style>
</head>
<body>

<!-- hero -->
<div class="abs hero" role="img" aria-label="Sunset sky over a grassy field with a wooden cross"></div>
<div class="abs service"><h4>SERVICE TIME</h4>Sunday Morning · 10:00 AM &nbsp; &amp; 6:00 PM<br>Wednesday · 7 PM</div>
<div class="abs brand"><div class="mark"></div><div class="name">Grace Harbor Church</div></div>
<nav class="abs nav"><span>HOME</span><span>LIBRARY</span><span class="pill">Donation</span></nav>
<h1 class="abs hero-title">Welcome to Grace<br>Harbor Church</h1>

<section class="abs band">
  <h2>Loving god and loving people</h2>
  <p>Lorem ipsum dolor sit amet, con sectetur adipiscing elit, sed do eiusmod tempor incididunt, con sectetur adi...</p>
</section>
<div class="abs donate-circle">Donate Now</div>

<!-- about -->
<div class="abs ghost about-ghost">About</div>
<h2 class="abs about-title">About Our<br>Church</h2>
<p class="abs about-lead">Lorem ipsum dolor sit amet, con sectetur adipiscing elit, sed do eiusmod tempor incididunt ut labore et e maua.</p>
<div class="abs about-mark" role="img" aria-label="Church emblem decoration"></div>
<div class="abs about-copy">
  <p>Lorem ipsum dolor sit amet, consectetur adipiscing elit, sed do eiusmod tempor incididunt ut labore et dolore magna aliqua. Quis ipsum suspendisse ultrices gravida. Risus commodo viverra maecenas accumsan lacus vel facilisis.</p>
  <p>Lorem ipsum dolor sit amet, consectetur adipiscing elit, sed do eiusmod tempor incididunt ut labore et dolore magna aliqua. Quis ipsum suspendisse ultrices gravida. Risus commodo viverra maecenas accumsan lacus vel facilisis.</p>
</div>

<!-- pastor -->
<section class="abs pastor"></section>
<div class="abs pastor-ghost">Pastor</div>
<h2 class="abs pastor-title">Pastor Bio</h2>
<p class="abs pastor-copy">Lorem ipsum dolor sit amet, consectetur adipiscing elit, sed do eiusmod tempor incididunt ut labore et dolore magna aliqua. Quis ipsum suspendisse ultrices gravida. Risus commodo viverra maecenas accumsan lacus vel facilisis.</p>
<span class="abs pill pastor-btn">View More</span>
<div class="abs pastor-photo" role="img" aria-label="Portrait of the pastor">800X800</div>

<!-- articles -->
<h2 class="abs articles-title">Articles of Faith</h2>
<div class="abs articles-ghost">Articles</div>

<article class="abs card one">
  <div class="photo" role="img" aria-label="Lit candles glowing in a dark chapel" style="background:linear-gradient(180deg,#3a2413,#a86a2a 60%,#f0b25a)"></div>
  <span class="date">Jan 25 2023</span>
  <h3>Lorem ipsum dolor sit amet, consectetur adipiscingu.</h3>
  <p>Lorem ipsum dolor sit amet, consectetur adipiscing elit, sed do eiusmod tempor incididunt ut labore et dolore magna aliqua sed.</p>
</article>
<article class="abs card two">
  <div class="photo" role="img" aria-label="Stone church tower lit at night" style="background:linear-gradient(180deg,#1d3f8a,#3c66b8 55%,#d6a13a)"></div>
  <span class="date">Jan 25 2023</span>
  <h3>Lorem ipsum dolor sit amet, consectetur adipiscingu.</h3>
  <p>Lorem ipsum dolor sit amet, consectetur adipiscing elit, sed do eiusmod tempor incididunt ut labore et dolore magna aliqua sed.</p>
</article>
<article class="abs card three">
  <div class="photo" role="img" aria-label="Cathedral interior with blue stained glass" style="background:linear-gradient(180deg,#142a5e,#2a4f9a 55%,#8a6b3a)"></div>
  <span class="date">Jan 25 2023</span>
  <h3>Lorem ipsum dolor sit amet, consectetur adipiscingu.</h3>
  <p>Lorem ipsum dolor sit amet, consectetur adipiscing elit, sed do eiusmod tempor incididunt ut labore et dolore magna aliqua sed.</p>
</article>
<span class="abs pill articles-btn">View All Articles</span>

<!-- announcements -->
<h2 class="abs ann-title">Announcements</h2>
<section class="abs ann-band"></section>
<div class="abs ann-photo" role="img" aria-label="Faded view of the church building"></div>
<h3 class="abs ann-heading">Returning to Live in-person<br>worship this Sunday!</h3>
<p class="abs ann-copy">Lorem ipsum dolor sit amet, conse ctetur adipiscing elit, sed do eiusmod tempor.</p>
<span class="abs pill ann-btn">Read More</span>
<form class="abs subscribe">
  <h3>Subscribe Now</h3>
  <div class="field">Name</div>
  <div class="field">Email</div>
  <span class="pill">Subscribe</span>
</form>

<!-- footer -->
<div class="abs foot-brand">
  <div class="mark"></div>
  <div class="name">Grace Harbor Church</div>
  <div class="socials"><span></span><span></span><span></span></div>
</div>
<div class="abs divider" style="left:372px"></div>
<div class="abs col" style="left:392px;width:260px">
  <h5>Mailing Address</h5>
  <div class="row">
    <svg width="14" height="18" viewBox="0 0 14 18"><path d="M7 0C3.1 0 0 3.1 0 7c0 5 7 11 7 11s7-6 7-11c0-3.9-3.1-7-7-7zm0 9.5A2.5 2.5 0 1 1 7 4.5a2.5 2.5 0 0 1 0 5z" fill="#6e7b3b"/></svg>
    <span>PO Box 4120<br>Maple Ridge 40210</span>
  </div>
  <h5 style="margin-top:14px">Contact</h5>
  <div class="row">
    <svg width="16" height="16" viewBox="0 0 16 16"><path d="M3.5 1l2.5 3-1.5 2c1 2 2.5 3.5 4.5 4.5l2-1.5 3 2.5-1.5 2.5C7 13.5 2.5 9 1 3z" fill="#6e7b3b"/></svg>
    <span>Phone<br>(555) 014-2290</span>
  </div>
  <div class="row">
    <svg width="16" height="14" viewBox="0 0 16 14"><rect x="0.5" y="1" width="15" height="12" rx="1.5" fill="none" stroke="#6e7b3b" stroke-width="1.5"/><path d="M1 2l7 6 7-6" fill="none" stroke="#6e7b3b" stroke-width="1.5"/></svg>
    <span>Email<br>hello@graceharborchurch.org</span>
  </div>
</div>
<div class="abs divider" style="left:680px"></div>
<div class="abs col" style="left:700px;width:180px">
  <h5>Resources</h5>
  <ul><li>Resources/Testimonials</li><li>Widening Grace</li><li>Sermons</li><li>Newsletter</li><li>Contact us</li></ul>
</div>
<div class="abs divider" style="left:900px"></div>
<div class="abs col" style="left:920px;width:180px">
  <h5>Links</h5>
  <ul><li>Events</li><li>Christian Education</li><li>Ministries &amp; Outreach</li><li>Music</li><li>Stewardship</li></ul>
</div>
<div class="abs bottom"></div>
<p class="abs copyright">GraceHarborChurch ©2023 All Rights are reserved Privacy Policy and Terms of Service apply.</p>
<span class="abs pill foot-donate">Donate Now</span>

</body>
</html>
```